American cannabis tech company business card design

Pavrel.com is seeking a modern, professional, and brand-aligned business card that represents our company and its core values: Mission, Story, Values, and Impact. As an innovative cannabis company, we want a business card that is not only visually appealing but also serves as a representation of who we are and what we stand for.

Project Scope: Design a double-sided business card that integrates our brand identity and core values. Incorporate our key brand elements, ensuring a sleek and contemporary aesthetic. Visually reflect our core values (Mission, Story, Values, Impact) in a way that is engaging yet professional.

Target Market(s)

Vendors, third parties,

Contact Information for Business Card

Contact details (name, title, email, phone, website, etc.)

Font styles to use
Other font styles liked:
• Caslon, Centra

Colors

Designer to choose colors to be used in the design.

Requirements
Must have
• Pavrel.com logo and branding A creative yet clean way to integrate our core values (Mission, Story, Values, Impact) Modern typography and a well-structured layout
Nice to have
• forest green, grey, white, black
Should not have
• references to marijuana, leafs, plants, or related product

```html
<!DOCTYPE html>
<html lang="en">
<head>
<meta charset="utf-8">
<title>Pavrel.com Business Card</title>
<link rel="stylesheet" href="https://fonts.googleapis.com/css2?family=Playfair+Display:wght@700;900&family=Montserrat:wght@400;500&display=swap">
<style>
  :root {
    --forest: #183620;
    --forest-deep: #14281a;
    --forest-mid: #1c4a2a;
    --forest-light: #236b3c;
    --paper: #ffffff;
    --ink: #1a1a1a;
    --backdrop: #d2d6d6;
  }
  * { box-sizing: border-box; margin: 0; padding: 0; }
  html, body { width: 1200px; height: 1050px; overflow: hidden; }
  body {
    background: var(--backdrop);
    font-family: "Montserrat", sans-serif;
    position: relative;
  }
  .card {
    position: absolute;
    left: 300px;
    width: 600px;
    height: 343px;
    overflow: hidden;
    box-shadow: 0 18px 40px rgba(0,0,0,0.18);
  }
  .card-front { top: 140px; background: var(--paper); }
  .card-back { top: 553px; background: var(--forest-deep); }

  .brand-name {
    position: absolute;
    top: 40px;
    right: 40px;
    font-family: "Playfair Display", serif;
    font-weight: 900;
    font-size: 80px;
    letter-spacing: -1px;
    line-height: 1;
    color: var(--forest);
  }
  .holder { position: absolute; left: 34px; top: 120px; }
  .holder-name {
    display: inline-block;
    font-family: "Playfair Display", serif;
    font-weight: 700;
    font-size: 20px;
    color: var(--forest);
    padding-bottom: 3px;
    border-bottom: 1.5px solid var(--forest);
  }
  .holder-title {
    display: block;
    font-family: "Playfair Display", serif;
    font-weight: 700;
    font-size: 9px;
    color: var(--forest);
    margin-top: 3px;
  }
  .contact-list {
    position: absolute;
    left: 34px;
    top: 176px;
    list-style: none;
  }
  .contact-list li {
    display: flex;
    align-items: center;
    gap: 8px;
    font-size: 12px;
    color: var(--ink);
    margin-bottom: 7px;
  }
  .contact-list svg { width: 11px; height: 11px; flex: none; }
  .icon-fill { fill: var(--forest); }
  .icon-line { fill: none; stroke: var(--forest); stroke-width: 2.4; }
  .divider {
    position: absolute;
    left: 150px;
    right: 34px;
    top: 262px;
    height: 1px;
    background: var(--forest);
  }
  .address {
    position: absolute;
    right: 34px;
    top: 272px;
    font-style: normal;
    font-size: 12px;
    line-height: 1.35;
    color: var(--ink);
  }
  .front-band {
    position: absolute;
    left: 0; right: 0; bottom: 0;
    height: 12px;
    background: var(--forest);
  }

  .back-pattern {
    position: absolute;
    inset: 0;
    background: linear-gradient(160deg, var(--forest-light) 0%, var(--forest-mid) 30%, var(--forest-deep) 70%);
  }
  .back-mark {
    position: absolute;
    left: 330px;
    top: 215px;
    font-family: "Playfair Display", serif;
    font-weight: 900;
    font-size: 30px;
    line-height: 1;
    color: var(--paper);
    letter-spacing: 0.5px;
  }
</style>
</head>
<body>
  <section class="card card-front" aria-label="Business card front">
    <div class="brand-name">PAVREL</div>

    <div class="holder">
      <span class="holder-name">Daniel Reyes</span>
      <span class="holder-title">Owner</span>
    </div>

    <ul class="contact-list">
      <li>
        <svg viewBox="0 0 24 24" aria-hidden="true"><path class="icon-fill" d="M6.6 10.8a15.1 15.1 0 0 0 6.6 6.6l2.2-2.2c.3-.3.7-.4 1-.2 1.1.4 2.3.6 3.6.6.6 0 1 .4 1 1V20c0 .6-.4 1-1 1A17 17 0 0 1 3 4c0-.6.4-1 1-1h3.5c.6 0 1 .4 1 1 0 1.3.2 2.5.6 3.6.1.3 0 .7-.2 1z"/></svg>
        555-014-0192
      </li>
      <li>
        <svg viewBox="0 0 24 24" aria-hidden="true"><rect class="icon-line" x="2.5" y="5" width="19" height="14"/><path class="icon-line" d="M2.5 5l9.5 8 9.5-8"/></svg>
        info@pavrel.com
      </li>
      <li>
        <svg viewBox="0 0 24 24" aria-hidden="true"><circle class="icon-line" cx="12" cy="12" r="9.5"/><path class="icon-line" d="M2.5 12h19M12 2.5c3 3 3 16 0 19M12 2.5c-3 3-3 16 0 19"/></svg>
        www.pavrel.com
      </li>
    </ul>

    <div class="divider"></div>

    <address class="address">
      418 Linden Ave, #112<br>
      Brookfield, OH 43210
    </address>

    <div class="front-band"></div>
  </section>

  <section class="card card-back" aria-label="Business card back">
    <div class="back-pattern" role="img" aria-label="Repeating brand-name texture in shades of forest green"></div>
    <div class="back-mark">PAVREL</div>
  </section>
</body>
</html>
```